TLK Electricial Contracting Services

Hi guys, after a design for my small electrical company, have logo design files to be incorporated into the layout, the basic concept is electrical contracting services for residential, commercial, industrial & data services, image is clean clear and strong,

Card format is to have a nice clean logo on front,with maybe the Residential – commercial – industrial - data, followed with licensed & insured, followed by contact details on backside of the card.

Target Market(s)

Residential, commercial, industrial sectors.

Industry/Entity Type

Electrical

Contact Information for Business Card

TLK logo,
Residential – commercial – industrial - data
REC: 61307
Email: tlk@vornamail.net.au
Phone: 0487 352 019

Requirements
Must have
• Clean & strong design.
Nice to have
• If possible, I would like the logo colours inverted so the text is orange and the background is black on the front of the card, then the backside of the card be the reverse colour
Should not have
• No Sparks, lightning bolts,

```html
<!DOCTYPE html>
<html lang="en">
<head>
<meta charset="utf-8">
<title>TLK Electrical – Business Card</title>
<link href="https://fonts.googleapis.com/css2?family=Orbitron:wght@700;900&family=Exo+2:ital,wght@0,500;1,400&display=swap" rel="stylesheet">
<style>
  :root {
    --orange: #f47a20;
    --black: #050505;
    --backdrop: #ececec;
  }
  * { margin: 0; padding: 0; box-sizing: border-box; }
  html, body { width: 1200px; height: 521px; overflow: hidden; }
  body { background: var(--backdrop); position: relative; font-family: "Exo 2", sans-serif; }

  .card {
    position: absolute;
    top: 112px;
    width: 520px;
    height: 297px;
    overflow: hidden;
  }
  .card--front { left: 60px; background: var(--black); color: var(--orange); }
  .card--back  { left: 623px; background: var(--orange); color: var(--black); }

  .edge-dot {
    position: absolute;
    top: 50%;
    width: 128px;
    height: 128px;
    margin-top: -64px;
    border-radius: 50%;
  }
  .card--front .edge-dot { left: -64px; background: var(--orange); }
  .card--back .edge-dot  { right: -64px; background: var(--black); }

  .brand-mark {
    font-family: "Orbitron", sans-serif;
    font-weight: 900;
    line-height: 1;
    letter-spacing: 2px;
  }
  .brand-name {
    font-family: "Orbitron", sans-serif;
    font-weight: 700;
    letter-spacing: 0.5px;
    white-space: nowrap;
  }

  .card--front .brand-mark {
    position: absolute; left: 0; right: 0; top: 58px;
    text-align: center; font-size: 92px; padding-left: 30px;
  }
  .card--front .brand-name {
    position: absolute; left: 0; right: 0; top: 156px;
    text-align: center; font-size: 17px; padding-left: 30px;
  }
  .tagline {
    position: absolute; left: 0; right: 0; top: 205px;
    text-align: center; font-style: italic; font-size: 16px; line-height: 20px;
  }

  .card--back .brand-mark {
    position: absolute; left: 18px; top: 20px; font-size: 66px;
  }
  .card--back .brand-name {
    position: absolute; left: 34px; top: 93px; font-size: 13px;
  }
  .services {
    position: absolute; left: 34px; top: 136px;
    list-style: none; font-size: 18px; font-weight: 500; line-height: 20px;
  }
  .services li::before { content: "•"; }
  .licence {
    position: absolute; left: 44px; top: 222px; font-size: 13px; font-weight: 500;
  }
  .contact {
    position: absolute; left: 272px; top: 218px;
    list-style: none; font-weight: 500;
  }
  .contact li { display: flex; align-items: center; gap: 7px; height: 28px; }
  .contact .phone { font-size: 22px; }
  .contact .email { font-size: 18px; }
  .contact svg { fill: var(--black); flex: none; }
</style>
</head>
<body>
  <section class="card card--front" aria-label="Card front">
    <div class="edge-dot"></div>
    <div class="brand-mark">TLK</div>
    <div class="brand-name">Tara Lee Knox Electrical</div>
    <p class="tagline">Electrical contracting services for residential,<br>commercial, industrial &amp; data services.</p>
  </section>

  <section class="card card--back" aria-label="Card back">
    <div class="edge-dot"></div>
    <div class="brand-mark">TLK</div>
    <div class="brand-name">Tara Lee Knox Electrical</div>
    <ul class="services">
      <li>Residential</li>
      <li>Commercial</li>
      <li>Industrial</li>
      <li>Data</li>
    </ul>
    <div class="licence">REC: 61307</div>
    <ul class="contact">
      <li class="phone">
        <svg width="18" height="16" viewBox="0 0 18 16" aria-hidden="true">
          <path d="M1 4 Q9 -1 17 4 L15 7 L12 6 L12 4 Q9 3 6 4 L6 6 L3 7 Z"/>
          <rect x="3" y="8" width="12" height="8" rx="1"/>
        </svg>
        0487.352.019
      </li>
      <li class="email">
        <svg width="18" height="14" viewBox="0 0 18 14" aria-hidden="true">
          <path d="M0 5 L9 0 L18 5 L18 14 L0 14 Z"/>
        </svg>
        tlk@vornamail.net.au
      </li>
    </ul>
  </section>
</body>
</html>
```